Website for software company "velora"

We need a website for our software company/startup named "velora". We are developing several products (currently 3 standard-software products) which are all in different sectors, but all our products are available for Laptops/PC/Mobile Phones/Tablets, ... We do also create custom software and support our customers with consulting to optimize their processes.
We already have a Logo which you can find in the attached files.
We are a young team of 4 members (two founders and 2 employees).

To get an idea of our products -> the first one is a planning software for healthcare organizations (eg. BlueHaven, firebrigade, pharmacy), the second one is a booking software for sport clubs and the third one is a competition software for sports hunting. You see very diverse. Include or ignore this info of our products as you like.

The design has to be a bootstrap 4 (or higher) design. We have licenced FontAwesome as iconset. Responsive design should come without saying.

• Starting page, product pages, news section, contact, team, services

```html
<!DOCTYPE html>
<html lang="en">
<head>
<meta charset="utf-8">
<title>velora — Software &amp; Consulting</title>
<link rel="stylesheet" href="https://fonts.googleapis.com/css2?family=Poppins:wght@400;500;600;700&display=swap">
<style>
:root{
  --orange:#f7822a;
  --orange-dark:#e96f14;
  --ink:#1d1f24;
  --text:#555a63;
  --muted:#8a8f98;
  --white:#ffffff;
  --light:#f1f1f1;
  --hero-a:#1c232c;
  --hero-b:#3a3f46;
  --navy:#0b1240;
  --navy-line:#2a3270;
}
*{box-sizing:border-box;margin:0;padding:0}
html,body{width:1200px;height:4840px;overflow:hidden}
body{font-family:"Poppins",Arial,sans-serif;color:var(--text);background:var(--white);position:relative}
.section{position:absolute;left:0;width:1200px}
.abs{position:absolute}
.btn{display:inline-flex;align-items:center;gap:10px;background:var(--orange);color:var(--white);font-size:13px;font-weight:500;padding:0 20px;height:40px;border-radius:3px}
.h2{font-size:32px;font-weight:700;color:var(--ink);line-height:1.2}
.h2.white{color:var(--white)}
.center{text-align:center}
p{font-size:14px;line-height:1.6}

/* top bar */
.topbar{top:0;height:40px;background:var(--orange);color:var(--white);font-size:12px}
.topbar .social{left:112px;top:11px;display:flex;gap:8px}
.topbar .social span{width:18px;height:18px;border-radius:50%;background:var(--white);display:block}
.topbar .contact{right:112px;top:0;height:40px;display:flex;align-items:center;gap:28px}
.topbar .contact span{display:flex;align-items:center;gap:6px}

/* nav */
.nav{top:40px;height:80px;background:var(--white)}
.logo{font-size:34px;font-weight:700;color:var(--ink);letter-spacing:1px;text-transform:uppercase}
.nav .logo{left:112px;top:16px}
.nav .menu{right:112px;top:20px;display:flex;gap:8px;list-style:none}
.nav .menu li{font-size:14px;color:var(--ink);padding:0 24px;height:40px;line-height:40px}
.nav .menu li.active{background:var(--orange);color:var(--white)}

/* hero */
.hero{top:120px;height:600px;overflow:hidden}
.hero .photo{inset:0;position:absolute;background:linear-gradient(100deg,var(--hero-a) 0%,#28303a 45%,#4b3526 52%,var(--hero-b) 70%,#252b33 100%)}
.hero h1{left:112px;top:52px;font-size:44px;line-height:1.25;font-weight:700;color:var(--white)}
.hero h1 em{font-style:normal;color:var(--orange)}
.hero p{left:112px;top:240px;width:360px;color:#e6e6e6;font-size:13px}
.hero .btn{left:112px;top:380px}
.hero .scroll{left:582px;top:492px;width:36px;height:48px;border:2px solid var(--white);border-radius:18px}
.hero .scroll::after{content:"";position:absolute;left:14px;top:12px;width:4px;height:10px;border-radius:2px;background:var(--white)}
.hero svg.curve{position:absolute;left:0;bottom:0}

/* welcome */
.welcome{top:720px;height:512px}
.welcome .h2{left:112px;top:136px}
.welcome p{left:112px;top:190px;width:490px;font-size:13px}
.welcome .more{left:112px;top:396px;font-size:13px;font-weight:600;color:var(--ink);letter-spacing:1px;display:flex;gap:12px;align-items:center}
.welcome .backdrop{left:644px;top:68px;width:120px;height:100px;background:var(--light)}
.welcome .photo{left:676px;top:92px;width:408px;height:316px;background:linear-gradient(135deg,#c9ccd1,#7d858f 55%,#3c4450)}

/* services */
.services{top:1232px;height:488px;background:var(--orange);color:var(--white)}
.services .h2{top:92px;left:0;width:100%}
.services .sub{top:132px;left:0;width:100%;font-size:15px;font-weight:500}
.services .lead{top:162px;left:250px;width:700px;font-size:12px;line-height:1.6}
.feature{top:276px;width:220px;text-align:center}
.feature .icon{width:48px;height:48px;border:2px solid var(--white);border-radius:6px;margin:0 auto 14px;display:flex;align-items:center;justify-content:center}
.feature h3{font-size:14px;font-weight:600;margin-bottom:6px}
.feature p{font-size:12px;line-height:1.5}

/* about */
.about{top:1720px;height:808px}
.about .h2{top:220px;width:100%}
.about p{top:268px;left:270px;width:660px;font-size:12px;text-align:center}
.about .photo{left:340px;top:360px;width:580px;height:370px;background:radial-gradient(ellipse at 50% 60%,#f2f2f4 0%,#dfe1e5 55%,#ffffff 100%)}

/* testimonials */
.testimonials{top:2528px;height:480px;background:var(--orange);color:var(--white)}
.testimonials .h2{left:112px;top:200px}
.testimonials .sub{left:112px;top:242px;font-size:12px}
.testimonials .quote-open{left:560px;top:96px}
.testimonials .quote-close{left:968px;top:256px}
.testimonials p{left:560px;top:140px;width:430px;font-size:12px}
.testimonials .avatar{left:560px;top:262px;width:44px;height:44px;border-radius:50%;background:#f5c9a4}
.testimonials .who{left:616px;top:264px}
.testimonials .who b{display:block;font-size:13px;font-weight:600}
.testimonials .who span{font-size:11px}
.testimonials .dots{left:560px;top:324px;display:flex;gap:6px}
.testimonials .dots i{width:8px;height:8px;border-radius:50%;background:rgba(255,255,255,.5);display:block}
.testimonials .dots i:first-child{background:var(--white);width:18px;border-radius:4px}

/* projects */
.projects{top:3008px;height:472px}
.projects .h2{top:84px;width:100%}
.project{top:160px;width:312px;height:264px;border-radius:8px;overflow:hidden;background:linear-gradient(160deg,#2b2f36,#121418)}
.project .inner{position:absolute;left:28px;top:140px;color:var(--white)}
.project h3{font-size:14px;font-weight:500;margin-top:12px;width:250px;line-height:1.4}

/* team */
.team{top:3480px;height:520px}
.team .h2{top:44px;width:100%}
.team .sub{top:88px;width:100%;font-size:14px;color:var(--ink)}
.member{top:152px;width:228px;height:320px;background:var(--light)}
.member .photo{height:248px;background:linear-gradient(180deg,#eceef0,#c3c7cd)}
.member .info{padding:14px 18px}
.member b{display:block;font-size:14px;font-weight:600;color:var(--ink)}
.member span{font-size:12px;color:var(--muted)}

/* call to action */
.cta{top:4000px;height:300px}
.cta .kicker{left:112px;top:110px;font-size:13px;color:var(--ink)}
.cta .h2{left:112px;top:130px}
.cta p{left:112px;top:180px;width:720px;font-size:13px}
.cta .btn{left:908px;top:180px}

/* footer */
.footer{top:4300px;height:540px;background:var(--navy);color:#cfd3e6}
.footer svg.top{position:absolute;left:0;top:0}
.footer .logo{left:112px;top:162px;color:var(--white)}
.fcol{top:112px;font-size:13px}
.fcol h4{font-size:14px;font-weight:600;color:var(--orange);margin-bottom:18px}
.fcol ul{list-style:none}
.fcol li{margin-bottom:10px;display:flex;align-items:center;gap:8px}
.fcol li::before{content:"";width:6px;height:2px;background:var(--orange)}
.fsep{top:112px;width:1px;height:230px;background:var(--navy-line)}
.fcontact{display:flex;gap:12px;margin-bottom:18px}
.fcontact .ic{width:26px;height:26px;border-radius:50%;background:var(--orange);flex:none}
.fcontact b{display:block;color:var(--orange);font-weight:500;font-size:12px}
.fcontact span{font-size:12px;color:var(--white)}
.subscribe{display:flex;margin:14px 0 16px}
.subscribe span{width:180px;height:36px;background:var(--white);border-radius:3px 0 0 3px;color:var(--muted);font-size:11px;line-height:36px;padding-left:12px}
.subscribe i{width:36px;height:36px;background:var(--orange);border-radius:0 3px 3px 0;display:block}
.fsocial{display:flex;gap:8px}
.fsocial span{width:28px;height:28px;border-radius:50%;background:var(--white);display:block}
.copyright{top:470px;width:100%;text-align:center;font-size:12px}
.copyright em{font-style:normal;color:var(--orange)}
.totop{left:1040px;top:462px;width:40px;height:40px;background:var(--white);display:flex;align-items:center;justify-content:center}
</style>
</head>
<body>

<header class="section topbar">
  <div class="abs social"><span></span><span></span><span></span><span></span></div>
  <div class="abs contact">
    <span><svg width="12" height="12" viewBox="0 0 24 24" fill="#fff"><path d="M6.6 10.8a15 15 0 0 0 6.6 6.6l2.2-2.2c.3-.3.7-.4 1-.2 1.1.4 2.3.6 3.6.6.6 0 1 .4 1 1V20c0 .6-.4 1-1 1A17 17 0 0 1 3 4c0-.6.4-1 1-1h3.5c.6 0 1 .4 1 1 0 1.3.2 2.5.6 3.6.1.3 0 .7-.2 1z"/></svg>+1 555 0142 7730</span>
    <span><svg width="12" height="12" viewBox="0 0 24 24" fill="#fff"><path d="M12 2a7 7 0 0 0-7 7c0 5 7 13 7 13s7-8 7-13a7 7 0 0 0-7-7zm0 9.5A2.5 2.5 0 1 1 12 6a2.5 2.5 0 0 1 0 5.5z"/></svg>Maple Lane Westbrook, Canada</span>
    <span><svg width="12" height="12" viewBox="0 0 24 24" fill="#fff"><path d="M2 5h20v14H2zm2 2v.5l8 5 8-5V7l-8 5z"/></svg>hello@velora.dev</span>
  </div>
</header>

<nav class="section nav">
  <div class="abs logo">velora</div>
  <ul class="abs menu">
    <li class="active">Home</li><li>Product</li><li>News</li><li>Contact</li><li>Team</li><li>Services</li>
  </ul>
</nav>

<section class="section hero">
  <div class="photo" role="img" aria-label="Dark office workspace photo with warm orange accent light"></div>
  <h1 class="abs">World Leading<br><em>Digital Marketing</em><br>Agency</h1>
  <p class="abs">Lorem ipsum dolor sit amet, consectetur adipiscing elit, sed do eiusmod tempor dolore magna aliqua. Quis ipsum suspendisse ultrices gravida. Risus commodo viverra maecenas accumsan lacus vel facilisis.</p>
  <span class="abs btn">Get Started Now <svg width="8" height="10" viewBox="0 0 8 10"><path d="M1 1l5 4-5 4" stroke="#fff" stroke-width="2" fill="none"/></svg></span>
  <div class="abs scroll"></div>
  <svg class="curve" width="1200" height="80" viewBox="0 0 1200 80">
    <path d="M0 40 Q600 100 1200 20 L1200 80 L0 80Z" fill="#fff"/>
    <path d="M0 40 Q600 100 1200 20" stroke="#f7822a" stroke-width="8" fill="none"/>
  </svg>
</section>

<section class="section welcome">
  <h2 class="abs h2">Welcome to Velora</h2>
  <p class="abs">Lorem ipsum dolor sit amet, consectetur adipiscing elit, sed do eiusmod tempor dolore magna aliqua. Quis ipsum suspendisse ultrices gravida. Risus commodo viverra maecenas accumsan lacus vel facilisis.Lorem ipsum dolor sit amet, consectetur adipiscing elit, sed do eiusmod tempor dolore magna aliqua. Quis ipsum suspendisse ultrices gravida. Risus commodo viverra maecenas accumsan lacus vel facilisis</p>
  <div class="abs more">LEARN MORE <svg width="18" height="10" viewBox="0 0 18 10"><path d="M0 5h16M12 1l4 4-4 4" stroke="#1d1f24" stroke-width="2" fill="none"/></svg></div>
  <div class="abs backdrop"></div>
  <div class="abs photo" role="img" aria-label="Photo of the business team standing together in suits"></div>
</section>

<section class="section services">
  <h2 class="abs h2 white center">Our Services</h2>
  <div class="abs sub center">With all the Features You Need</div>
  <p class="abs lead center">Lorem ipsum dolor sit amet, consectetur adipiscing elit, sed do eiusmod tempor dolore magna aliqua. Quis ipsum suspendisse ultrices gravida. Risus commodo viverra maecenas accumsan lacus vel facilisis.Lorem ipsum dolor sit amet, consectetur</p>
  <div class="abs feature" style="left:190px">
    <div class="icon"><svg width="24" height="24" viewBox="0 0 24 24" fill="none" stroke="#fff" stroke-width="2"><path d="M4 20V10M10 20V4M16 20v-7M22 20H2"/></svg></div>
    <h3>Good Performance</h3>
    <p>Lorem ipsum dolor sit amet, consectetur adipiscing elit, sed do eiusmod tempor dolore magna aliqua. Quis ipsum suspendisse ultrices gravida.</p>
  </div>
  <div class="abs feature" style="left:490px">
    <div class="icon"><svg width="24" height="24" viewBox="0 0 24 24" fill="none" stroke="#fff" stroke-width="2"><rect x="5" y="11" width="14" height="10" rx="1"/><path d="M8 11V7a4 4 0 0 1 8 0v4"/></svg></div>
    <h3>Highly Secure</h3>
    <p>Appropriately grow competitive leadership rather than strategic technically sound processes without value.</p>
  </div>
  <div class="abs feature" style="left:790px">
    <div class="icon"><svg width="24" height="24" viewBox="0 0 24 24" fill="none" stroke="#fff" stroke-width="2"><rect x="2" y="4" width="20" height="13" rx="1"/><path d="M8 21h8M12 17v4M9 9l-2 2 2 2M15 9l2 2-2 2"/></svg></div>
    <h3>Fast Development</h3>
    <p>Lorem ipsum dolor sit amet, consectetur adipiscing elit, sed do eiusmod tempor dolore magna aliqua. Quis ipsum suspendisse ultrices gravida.</p>
  </div>
</section>

<section class="section about">
  <h2 class="abs h2 center">About Us</h2>
  <p class="abs">Lorem ipsum dolor sit amet, consectetur adipiscing elit, sed do eiusmod tempor dolore magna aliqua. Quis ipsum suspendisse ultrices gravida. Risus commodo viverra maecenas accumsan lacus vel facilisis.Lorem ipsum dolor sit amet, consectetur</p>
  <div class="abs photo" role="img" aria-label="Portrait composition of the two company founders"></div>
</section>

<section class="section testimonials">
  <h2 class="abs h2 white">Testimonials</h2>
  <div class="abs sub">Our Customer Valuable Feedback</div>
  <svg class="abs quote-open" width="30" height="24" viewBox="0 0 30 24" fill="#fff"><path d="M0 24V12L6 0h6L8 12h5v12zM17 24V12L23 0h6l-4 12h5v12z"/></svg>
  <p class="abs">Lorem ipsum dolor sit amet, consectetur adipiscing elit, sed do eiusmod tempor dolore magna aliqua. Quis ipsum suspendisse ultrices gravida. Risus commodo viverra maecenas accumsan lacus vel facilisis.Lorem ipsum dolor sit amet, consectetur</p>
  <svg class="abs quote-close" width="40" height="32" viewBox="0 0 30 24" fill="rgba(255,255,255,.55)"><path d="M30 0v12l-6 12h-6l4-12h-5V0zM13 0v12L7 24H1l4-12H0V0z"/></svg>
  <div class="abs avatar" role="img" aria-label="Customer portrait"></div>
  <div class="abs who"><b>Mark Ellison</b><span>Managing director of company</span></div>
  <div class="abs dots"><i></i><i></i><i></i></div>
</section>

<section class="section projects">
  <h2 class="abs h2 center">Projects We Worked On</h2>
  <div class="abs project" style="left:112px" role="img" aria-label="Dark photo of a healthcare planning workspace">
    <div class="inner"><svg width="44" height="40" viewBox="0 0 24 22" fill="none" stroke="#f7822a" stroke-width="1.5"><rect x="1" y="1" width="22" height="14" rx="1"/><path d="M8 21h8M12 15v6M4 10l3-3 3 4 3-5 3 4 3-2"/></svg><h3>Healthcare organizations</h3></div>
  </div>
  <div class="abs project" style="left:444px" role="img" aria-label="Dark photo of a sports club booking setup">
    <div class="inner"><svg width="44" height="40" viewBox="0 0 24 22" fill="none" stroke="#f7822a" stroke-width="1.5"><rect x="1" y="1" width="22" height="14" rx="1"/><path d="M8 21h8M12 15v6M6 11V8M10 11V5M14 11V7M18 11V4"/></svg><h3>Software for sport clubs</h3></div>
  </div>
  <div class="abs project" style="left:776px" role="img" aria-label="Dark photo of a competition scoring screen">
    <div class="inner"><svg width="44" height="40" viewBox="0 0 24 22" fill="none" stroke="#f7822a" stroke-width="1.5"><rect x="1" y="1" width="22" height="14" rx="1"/><path d="M8 21h8M12 15v6"/><circle cx="12" cy="8" r="4"/><path d="M12 3v10M7 8h10"/></svg><h3>Competition software for sports hunting</h3></div>
  </div>
</section>

<section class="section team">
  <h2 class="abs h2 center">Our Team</h2>
  <div class="abs sub center">We Help To Achieve Your Business Goal</div>
  <div class="abs member" style="left:112px"><div class="photo" role="img" aria-label="Portrait of a founder"></div><div class="info"><b>Daniel Hart</b><span>CEO &amp; Founder</span></div></div>
  <div class="abs member" style="left:364px"><div class="photo" role="img" aria-label="Portrait of a founder"></div><div class="info"><b>Daniel Hart</b><span>CEO &amp; Founder</span></div></div>
  <div class="abs member" style="left:612px"><div class="photo" role="img" aria-label="Portrait of an employee"></div><div class="info"><b>Daniel Hart</b><span>Employee</span></div></div>
  <div class="abs member" style="left:860px"><div class="photo" role="img" aria-label="Portrait of an employee"></div><div class="info"><b>Daniel Hart</b><span>Employee</span></div></div>
</section>

<section class="section cta">
  <div class="abs kicker">Let's Talk</div>
  <h2 class="abs h2">Get Started A Project?</h2>
  <p class="abs">Lorem ipsum dolor sit amet, consectetur adipiscing elit, sed do eiusmod tempor dolore magna aliqua. Quis ipsum suspendisse ultrices gravida. Risus commodo viverra maecenas accumsan lacus vel facilisis.Lorem ipsum dolor sit amet, consectetur</p>
  <span class="abs btn">Get Started Now <svg width="8" height="10" viewBox="0 0 8 10"><path d="M1 1l5 4-5 4" stroke="#fff" stroke-width="2" fill="none"/></svg></span>
</section>

<footer class="section footer">
  <svg class="top" width="1200" height="60" viewBox="0 0 1200 60"><path d="M0 0H1200V10Q600 70 0 10Z" fill="#fff"/></svg>
  <div class="abs logo">velora</div>
  <div class="abs fsep" style="left:360px"></div>
  <div class="abs fcol" style="left:400px">
    <h4>Sitemap</h4>
    <ul><li>Home</li><li>Product</li><li>News</li><li>Contact</li><li>Team</li><li>Services</li></ul>
  </div>
  <div class="abs fsep" style="left:528px"></div>
  <div class="abs fcol" style="left:560px">
    <h4>Contact Us</h4>
    <div class="fcontact"><span class="ic"></span><div><b>Address</b><span>Westbrook, TX 70112</span></div></div>
    <div class="fcontact"><span class="ic"></span><div><b>E-mail</b><span>support@velora.dev</span></div></div>
    <div class="fcontact"><span class="ic"></span><div><b>Contact</b><span>+44-20-7946-0321</span></div></div>
  </div>
  <div class="abs fsep" style="left:780px"></div>
  <div class="abs fcol" style="left:820px;width:260px">
    <h4>Subscribe to our Newsletter</h4>
    <div style="font-size:11px;line-height:1.5">When an unknown printer took a galley of type and scrambled</div>
    <div class="subscribe"><span>Email Address</span><i></i></div>
    <div class="fsocial"><span></span><span></span><span></span><span></span></div>
  </div>
  <div class="abs copyright">Copyright © 2022 <em>Velora</em> . All rights reserved.</div>
  <div class="abs totop"><svg width="14" height="10" viewBox="0 0 14 10"><path d="M1 8l6-6 6 6" stroke="#0b1240" stroke-width="2" fill="none"/></svg></div>
</footer>

</body>
</html>
```